Young, dynamic furniture company needs a new business card design

We require a new business card design for our modern furniture company which supplies furniture and appliances to the property and development market.
Oakridge Interiors has become one of the leading furniture & appliance suppliers to the property market withing London. With over 10 years experience, we have increased our business to supply not only private landlords and managing agents, but also property developers, housing associations and local councils.
We offer not only a complete range of furniture which includes beds, wardrobes, dining sets and sofas, but also a high quality, full delivery and assembly service to help you with all our furnishing needs.

Target Market(s)

Private landlords, estate agents, letting agents, property management companies

Industry/Entity Type

Business

Contact Information for Business Card

Name,
Title,
Address,
Mobile,
Telephone,
Fax, Website, email address

Font styles to use
Sans Serif

Colors
3176b5
0555a3
85abd2
cfdeed

Requirements
Must have
• All the above information for each of our staff, along with our logo

```html
<!DOCTYPE html>
<html lang="en">
<head>
<meta charset="utf-8">
<title>Oakridge Interiors – Business Card</title>
<link rel="stylesheet" href="https://fonts.googleapis.com/css2?family=Roboto:wght@300;400&family=Open+Sans:wght@400;600;700&display=swap">
<style>
  :root {
    --bg: #c9c8c6;
    --card: #ffffff;
    --navy: #213b72;
    --blue: #1a6fb5;
    --ink: #1f1f1f;
    --grey: #4a4a4a;
    --name-blue: #2d5aa8;
    --rule: #2d4f96;
  }
  * { margin: 0; padding: 0; box-sizing: border-box; }
  html, body { width: 1200px; height: 994px; overflow: hidden; background: var(--bg); }
  .canvas { position: relative; width: 1200px; height: 994px; }

  .card {
    position: absolute; left: 250px; width: 700px; height: 400px;
    background: var(--card); overflow: hidden;
    box-shadow: 0 10px 24px rgba(0,0,0,0.22);
  }
  .card--front { top: 70px; }
  .card--back { top: 524px; }
  .card__band { position: absolute; inset: 0; width: 700px; height: 400px; }

  .brand { position: absolute; display: flex; flex-direction: column; align-items: flex-start; }
  .brand__row { display: flex; align-items: center; gap: 12px; }
  .brand__square { width: 26px; height: 26px; background: var(--blue); }
  .brand__name {
    font-family: "Roboto", sans-serif; font-weight: 400; font-size: 34px;
    color: var(--ink); text-transform: uppercase; letter-spacing: 0.5px; line-height: 1;
  }
  .brand__tagline {
    font-family: "Roboto", sans-serif; font-weight: 300; font-size: 17px;
    color: var(--grey); text-transform: uppercase; margin: 6px 0 0 38px; letter-spacing: 0.3px;
  }
  .card--front .brand { left: 150px; top: 272px; }
  .card--back .brand { left: 330px; top: 262px; }

  .person { position: absolute; left: 54px; top: 60px; font-family: "Open Sans", sans-serif; }
  .person__name { font-size: 28px; font-weight: 700; color: var(--name-blue); line-height: 1.1; }
  .person__role { font-size: 15px; font-weight: 700; color: var(--navy); margin-top: 4px; }

  .contact { position: absolute; left: 54px; top: 226px; font-family: "Open Sans", sans-serif; }
  .contact__list { list-style: none; }
  .contact__item { display: flex; align-items: center; gap: 10px; font-size: 16px; color: var(--ink); line-height: 22px; }
  .contact__icon { width: 15px; height: 15px; fill: var(--navy); flex: none; }
  .contact__rule { width: 300px; height: 1.5px; background: var(--rule); margin: 8px 0 6px; }
  .contact__address { font-size: 16px; color: var(--navy); line-height: 21px; font-weight: 600; }
</style>
</head>
<body>
<main class="canvas">

  <section class="card card--front" aria-label="Card front">
    <svg class="card__band" viewBox="0 0 700 400" aria-hidden="true">
      <polygon points="0,0 700,0 700,285 0,18" fill="var(--navy)"/>
    </svg>
    <div class="brand">
      <div class="brand__row">
        <span class="brand__square"></span>
        <span class="brand__name">Oakridge Interiors</span>
      </div>
      <span class="brand__tagline">Trade Furniture Solutions</span>
    </div>
  </section>

  <section class="card card--back" aria-label="Card back">
    <svg class="card__band" viewBox="0 0 700 400" aria-hidden="true">
      <polygon points="336,0 700,0 700,182" fill="var(--navy)"/>
    </svg>

    <div class="person">
      <p class="person__name">YOUR NAME</p>
      <p class="person__role">POSITION</p>
    </div>

    <div class="brand">
      <div class="brand__row">
        <span class="brand__square"></span>
        <span class="brand__name">Oakridge Interiors</span>
      </div>
      <span class="brand__tagline">Trade Furniture Solutions</span>
    </div>

    <div class="contact">
      <ul class="contact__list">
        <li class="contact__item">
          <svg class="contact__icon" viewBox="0 0 16 16" aria-hidden="true"><path d="M3 1h3l1.5 4-2 1.2a8 8 0 0 0 4.3 4.3L11 8.5l4 1.5v3a2 2 0 0 1-2 2A12 12 0 0 1 1 3a2 2 0 0 1 2-2z"/></svg>
          123-456-7890
        </li>
        <li class="contact__item">
          <svg class="contact__icon" viewBox="0 0 16 16" aria-hidden="true"><rect x="4" y="1" width="8" height="5"/><rect x="1" y="6" width="14" height="6" rx="1"/><rect x="4" y="10" width="8" height="5"/></svg>
          123-456-7890
        </li>
        <li class="contact__item">
          <svg class="contact__icon" viewBox="0 0 16 16" aria-hidden="true"><path d="M1 3h14v10H1z M1 3l7 6 7-6" stroke="#fff" stroke-width="1"/></svg>
          youremail@mailbox.com
        </li>
        <li class="contact__item">
          <svg class="contact__icon" viewBox="0 0 16 16" aria-hidden="true"><circle cx="8" cy="8" r="7"/><path d="M1 8h14M8 1v14M3 4h10M3 12h10" stroke="#fff" stroke-width="0.9" fill="none"/><ellipse cx="8" cy="8" rx="3" ry="7" fill="none" stroke="#fff" stroke-width="0.9"/></svg>
          www.website.com
        </li>
      </ul>
      <div class="contact__rule"></div>
      <p class="contact__address">PO BOX 1234, Address Line 1,<br>Address Line 2,</p>
    </div>
  </section>

</main>
</body>
</html>
```